Kestrel Facilities Business Card Design

We would now like to design business cards with the new Kestrel Facilities logo

Target Market(s)

Professional

Industry/Entity Type

Professional services

Contact Information for Business Card

Employee name, title, phone number, email address, corporate office address and logo.

Font styles to use
Sans Serif

Colors
0054AA
0677BA
7BADD7
CADEEF
E8F1F8

Requirements
Must have
• My logo
Should not have
• any other pictures or images besides my logo

```html
<!DOCTYPE html>
<html lang="en">
<head>
<meta charset="utf-8">
<title>Kestrel Facilities – Business Card</title>
<link rel="stylesheet" href="https://fonts.googleapis.com/css2?family=Oswald:wght@500&family=Open+Sans:wght@400;600&display=swap">
<style>
  :root {
    --page-bg: #2a2a2a;
    --card-bg: #1b1b1b;
    --card-edge: #111111;
    --emboss: #0b0b0b;
    --brand-blue: #0a7fe6;
    --text-light: #e6e6e6;
    --text-muted: #cfcfcf;
  }
  * { box-sizing: border-box; margin: 0; padding: 0; }
  html, body { width: 1200px; height: 1015px; overflow: hidden; }
  body {
    background: var(--page-bg);
    font-family: "Open Sans", Arial, sans-serif;
    position: relative;
  }
  .card {
    position: absolute;
    left: 230px;
    width: 740px;
    height: 423px;
    background: var(--card-bg);
    border: 1px solid var(--card-edge);
    box-shadow: 0 18px 40px rgba(0,0,0,.55);
    overflow: hidden;
  }
  .card--back { top: 48px; }
  .card--front { top: 530px; }

  /* back */
  .back-wordmark {
    position: absolute;
    inset: 0;
    display: flex;
    align-items: center;
    justify-content: center;
    gap: 22px;
  }
  .back-wordmark .mark-square {
    width: 54px; height: 54px;
    background: var(--emboss);
  }
  .back-wordmark .brand-name {
    font-weight: 600;
    font-size: 50px;
    letter-spacing: 1px;
    color: var(--emboss);
  }

  /* front */
  .identity {
    position: absolute;
    left: 60px;
    top: 92px;
  }
  .person-name {
    font-family: "Oswald", "Arial Narrow", sans-serif;
    font-weight: 500;
    font-size: 34px;
    line-height: 1;
    color: var(--brand-blue);
    text-transform: uppercase;
  }
  .person-title {
    margin-top: 6px;
    font-size: 19px;
    color: var(--text-light);
  }
  .contact-list {
    position: absolute;
    left: 60px;
    top: 196px;
    list-style: none;
  }
  .contact-list li {
    display: flex;
    align-items: center;
    gap: 12px;
    font-size: 18px;
    line-height: 27px;
    color: var(--text-light);
  }
  .contact-list svg { width: 18px; height: 18px; fill: var(--brand-blue); flex: none; }
  .contact-list .accent { color: var(--brand-blue); }
  .address {
    position: absolute;
    left: 90px;
    top: 318px;
    font-size: 18px;
    line-height: 25px;
    color: var(--text-muted);
  }
  .front-wordmark {
    position: absolute;
    right: 48px;
    top: 0;
    bottom: 0;
    width: 330px;
    display: flex;
    flex-direction: column;
    align-items: center;
    justify-content: center;
    gap: 18px;
  }
  .front-wordmark .mark-square {
    width: 110px; height: 110px;
    border: 16px solid var(--brand-blue);
  }
  .front-wordmark .brand-name {
    font-weight: 600;
    font-size: 34px;
    color: var(--brand-blue);
    text-align: center;
  }
</style>
</head>
<body>

<section class="card card--back" aria-label="Card back">
  <div class="back-wordmark">
    <span class="mark-square"></span>
    <span class="brand-name">Kestrel Facilities</span>
  </div>
</section>

<section class="card card--front" aria-label="Card front">
  <div class="identity">
    <p class="person-name">Martin Hale</p>
    <p class="person-title">Managing Director</p>
  </div>

  <ul class="contact-list">
    <li>
      <svg viewBox="0 0 24 24" aria-hidden="true"><path d="M6.6 10.8a15.1 15.1 0 0 0 6.6 6.6l2.2-2.2c.3-.3.7-.4 1-.2 1.1.4 2.3.6 3.6.6.6 0 1 .4 1 1V20c0 .6-.4 1-1 1A17 17 0 0 1 3 4c0-.6.4-1 1-1h3.5c.6 0 1 .4 1 1 0 1.3.2 2.5.6 3.6.1.3 0 .7-.2 1z"/></svg>
      044-555 010 234
    </li>
    <li>
      <svg viewBox="0 0 24 24" aria-hidden="true"><path d="M2 5h20v14H2zm2 2v.4l8 5.2 8-5.2V7zm0 2.8V17h16V9.8l-8 5.2z"/></svg>
      info@kestrelfm.com
    </li>
    <li>
      <svg viewBox="0 0 24 24" aria-hidden="true"><path d="M12 2a10 10 0 1 0 0 20 10 10 0 0 0 0-20zm6.9 6h-2.9a15 15 0 0 0-1.4-3.6A8 8 0 0 1 18.9 8zM12 4c.8 1.2 1.5 2.5 1.9 4h-3.8c.4-1.5 1.1-2.8 1.9-4zM4.3 14a8 8 0 0 1 0-4h3.3a16 16 0 0 0 0 4zm.8 2h2.9c.3 1.3.8 2.5 1.4 3.6A8 8 0 0 1 5.1 16zM8 8H5.1a8 8 0 0 1 4.3-3.6C8.8 5.5 8.3 6.7 8 8zm4 12c-.8-1.2-1.5-2.5-1.9-4h3.8c-.4 1.5-1.1 2.8-1.9 4zm2.3-6H9.7a14 14 0 0 1 0-4h4.6a14 14 0 0 1 0 4zm.3 5.6c.6-1.1 1.1-2.3 1.4-3.6h2.9a8 8 0 0 1-4.3 3.6zm1.8-5.6a16 16 0 0 0 0-4h3.3a8 8 0 0 1 0 4z"/></svg>
      <span>www.<span class="accent">kestrelfm</span>.com</span>
    </li>
  </ul>

  <p class="address">88, Harbour Row, Suite 4<br>20418, Northvale</p>

  <div class="front-wordmark">
    <span class="mark-square"></span>
    <span class="brand-name">Kestrel Facilities</span>
  </div>
</section>

</body>
</html>
```